Brand Identity Stationary Package

Hello I'm looking for a full branding package for my Property Management Company. I have a logo but looking to have the following
Business Card
Email signature
Facebook cover photo
Letterhead (word.doc)
#10 Envelope
Pocket Folder - link to 9x12 pocket folder design specs https://www.printorbit-example.ca/marketing-materials/presentation-folders
would like everything to match and be brand identifiable. The company looks after residential properties/apartments and some commercial properties. Attached is a zip of the files.
For Business Card
Name: Gareth Lindqvist
Position: Operations Manager
Number: 1 (555) 384-2917
Email: Gareth@harborkey-example.ca
Website: Harborkey-example.ca
Property Management

```html
<!DOCTYPE html>
<html lang="en">
<head>
<meta charset="utf-8">
<title>Harborkey Stationery Package</title>
<link rel="stylesheet" href="https://fonts.googleapis.com/css2?family=Montserrat:wght@600&family=Open+Sans:wght@400&family=Roboto:wght@400;500&display=swap">
<style>
:root{
  --bg:#ececec;
  --paper:#f3f3f3;
  --ink:#222222;
  --dark:#1f1f1f;
  --green:#79a83c;
  --text:#555555;
  --white:#ffffff;
  --faint:#e4e4e4;
  --placeholder:#4a4a4a;
}
*{margin:0;padding:0;box-sizing:border-box}
html,body{width:1200px;height:795px;overflow:hidden;background:var(--bg)}
.canvas{position:relative;width:1200px;height:795px}
.brand{font-family:"Montserrat",sans-serif;font-weight:600;letter-spacing:.12em;white-space:nowrap;line-height:1}

/* Letterhead */
.letterhead{position:absolute;left:293px;top:99px;width:293px;height:415px;background:var(--paper)}
.letterhead .brand{position:absolute;top:28px;left:0;width:100%;text-align:center;font-size:15px;color:var(--ink)}
.letter-body{position:absolute;left:31px;top:106px;width:230px;font-family:"Open Sans",sans-serif;font-size:4.5px;line-height:7.6px;color:var(--text);text-align:justify}
.letter-body p{margin-bottom:7.6px}
.letter-footer{position:absolute;left:0;top:381px;width:100%;text-align:center;font-family:"Roboto",sans-serif;font-size:6.3px;line-height:9px;color:var(--text)}
.letter-footer .icon{display:inline-block;width:5px;height:5px;vertical-align:-0.5px;margin:0 1px 0 3px}

/* Folder */
.folder{position:absolute;left:637px;top:80px;width:347px;height:437px;background:var(--dark);overflow:hidden}
.folder .brand{position:absolute;top:105px;left:0;width:100%;text-align:center;font-size:27px;color:var(--white)}
.folder-photo{position:absolute;left:0;top:218px;width:100%;height:219px;background:var(--placeholder)}

/* Business cards */
.card{position:absolute;left:187px;width:132px;height:75px;background:var(--dark)}
.card-front{top:551px}
.card-front .brand{position:absolute;top:28px;width:100%;text-align:center;font-size:12px;color:var(--white)}
.card-front .card-web{position:absolute;top:63px;width:100%;text-align:center;font-family:"Roboto",sans-serif;font-size:4.2px;color:var(--white);letter-spacing:.05em}
.card-back{top:647px}
.card-back .brand{position:absolute;top:13px;right:12px;font-size:8px;color:var(--white)}
.card-back .accent{position:absolute;left:0;top:39px;width:3px;height:8px;background:var(--green)}
.card-back .name{position:absolute;left:11px;top:38px;font-family:"Roboto",sans-serif;font-weight:500;font-size:4.6px;color:var(--green)}
.card-back .role{position:absolute;left:11px;top:44px;font-family:"Roboto",sans-serif;font-size:3.6px;color:var(--white)}
.card-back .rule{position:absolute;left:11px;right:12px;top:49.5px;height:.5px;background:#777}
.card-back .contact{position:absolute;left:11px;top:54px;font-family:"Roboto",sans-serif;font-size:3.5px;line-height:5px;color:var(--white)}
.card-back .contact .icon{display:inline-block;width:3.5px;height:3.5px;margin-right:1.5px;vertical-align:-0.5px}
.card-back .address{position:absolute;right:12px;top:54px;text-align:right;font-family:"Roboto",sans-serif;font-size:3.5px;line-height:5px;color:var(--white)}
.card-back .address .company{color:var(--green)}

/* Envelopes */
.envelope-front{position:absolute;left:353px;top:562px;width:329px;height:157px;background:var(--paper)}
.envelope-front .brand{position:absolute;left:21px;top:27px;width:96px;text-align:center;font-size:12px;color:var(--ink)}
.envelope-front .return-address{position:absolute;left:16px;top:46px;width:106px;text-align:center;font-family:"Roboto",sans-serif;font-size:6.4px;line-height:7.6px;color:var(--text)}
.envelope-front .window{position:absolute;right:0;top:4px;width:114px;height:125px;background:var(--faint)}
.envelope-back{position:absolute;left:713px;top:561px;width:329px;height:157px;background:var(--paper)}
.envelope-back .flap{position:absolute;left:0;top:0}
.envelope-back .brand{position:absolute;top:20px;width:100%;text-align:center;font-size:11px;color:var(--white)}
</style>
</head>
<body>
<main class="canvas">

  <section class="letterhead" aria-label="Letterhead">
    <div class="brand">HARBORKEY</div>
    <div class="letter-body">
      <p>Dear customer,</p>
      <p>Lorem ipsum dolor sit amet, consectetur adipisicing elit, sed do eiusmod tempor incididunt ut labore et dolore magna aliqua. Ut enim ad minim veniam, quis nostrud exercitation ullamco laboris nisi ut aliquip ex ea commodo consequat. Duis aute irure dolor in reprehenderit in voluptate velit esse cillum dolore eu fugiat nulla pariatur. Excepteur sint occaecat cupidatat non proident, sunt in culpa qui officia deserunt mollit anim id est laborum.</p>
      <p>Lorem ipsum dolor sit amet, consectetur adipisicing elit, sed do eiusmod tempor incididunt ut labore et dolore magna aliqua. Ut enim ad minim veniam, quis nostrud exercitation ullamco laboris nisi ut aliquip ex ea commodo consequat. Duis aute irure dolor in reprehenderit in voluptate velit esse cillum dolore eu fugiat nulla pariatur. Excepteur sint occaecat cupidatat non proident, sunt in culpa qui officia deserunt mollit anim id est laborum.</p>
      <p>Lorem ipsum dolor sit amet, consectetur adipisicing elit, sed do eiusmod tempor incididunt ut labore et dolore magna aliqua. Ut enim ad minim veniam, quis nostrud exercitation ullamco laboris nisi ut aliquip ex ea commodo consequat. Duis aute irure dolor in reprehenderit in voluptate velit esse cillum dolore eu fugiat nulla pariatur. Excepteur sint occaecat cupidatat non proident, sunt in culpa qui officia deserunt mollit anim id est laborum.</p>
      <p>Lorem ipsum dolor sit amet, consectetur adipisicing elit, sed do eiusmod tempor incididunt ut labore et dolore magna aliqua. Ut enim ad minim veniam, quis nostrud exercitation ullamco laboris nisi ut aliquip ex ea commodo consequat. Duis aute irure dolor in reprehenderit.</p>
      <p>Yours Sincerely,</p>
    </div>
    <div class="letter-footer">
      <div>48 Alder Crest Road,&nbsp; Maple Hollow, ON K0X 3B7</div>
      <div>
        <svg class="icon" viewBox="0 0 10 10"><path d="M2 1l2 0 1 2.5-1.3 1a5 5 0 0 0 2.8 2.8l1-1.3 2.5 1v2c-5 0-8-3-8-8z" fill="#79a83c"/></svg>1 (555) 384-2917
        <svg class="icon" viewBox="0 0 10 10"><rect x="0.5" y="2" width="9" height="6.5" fill="#79a83c"/><path d="M0.5 2l4.5 3.5 4.5-3.5" stroke="#f3f3f3" fill="none" stroke-width="0.8"/></svg>Gareth@harborkey-example.ca
        <svg class="icon" viewBox="0 0 10 10"><circle cx="5" cy="5" r="4.3" fill="none" stroke="#79a83c" stroke-width="1.2"/><path d="M1 5h8M5 .7v8.6" stroke="#79a83c" stroke-width=".8"/></svg>www.harborkey-example.ca
      </div>
    </div>
  </section>

  <section class="folder" aria-label="Pocket folder cover">
    <div class="brand">HARBORKEY</div>
    <div class="folder-photo" role="img" aria-label="Architectural photograph of a modern building corner"></div>
  </section>

  <section class="card card-front" aria-label="Business card front">
    <div class="brand">HARBORKEY</div>
    <div class="card-web">www.harborkey-example.ca</div>
  </section>

  <section class="card card-back" aria-label="Business card back">
    <div class="brand">HARBORKEY</div>
    <div class="accent"></div>
    <div class="name">GARETH LINDQVIST</div>
    <div class="role">Operations Manager</div>
    <div class="rule"></div>
    <div class="contact">
      <div><svg class="icon" viewBox="0 0 10 10"><path d="M2 1l2 0 1 2.5-1.3 1a5 5 0 0 0 2.8 2.8l1-1.3 2.5 1v2c-5 0-8-3-8-8z" fill="#79a83c"/></svg>1 (555) 384-2917</div>
      <div><svg class="icon" viewBox="0 0 10 10"><rect x="0.5" y="2" width="9" height="6.5" fill="#79a83c"/></svg>Gareth@harborkey-example.ca</div>
      <div><svg class="icon" viewBox="0 0 10 10"><circle cx="5" cy="5" r="4" fill="none" stroke="#79a83c" stroke-width="1.2"/></svg>www.harborkey-example.ca</div>
    </div>
    <div class="address">
      <div class="company">Harborkey, Ltd</div>
      <div>48 Alder Crest Road</div>
      <div>Maple Hollow, ON K0X 3B7</div>
    </div>
  </section>

  <section class="envelope-front" aria-label="Envelope front">
    <div class="brand">HARBORKEY</div>
    <div class="return-address">Unit 7 / 12 Tidewater Lane,<br>Kestrel Bay, NSW 2999</div>
    <div class="window"></div>
  </section>

  <section class="envelope-back" aria-label="Envelope back">
    <svg class="flap" width="329" height="57" viewBox="0 0 329 57">
      <path d="M0 0H329L322 48Q321 55 313 55H15Q8 55 7 48Z" fill="#1f1f1f"/>
    </svg>
    <div class="brand">HARBORKEY</div>
  </section>

</main>
</body>
</html>
```